Clear Plastic Card Design

I am looking to have a business card designed from my logo icon. I am looking to match the style of a different business card I have attached in the files.
Looking for a card that is plastic, with layers of transparency in the shape of my logo icon (also attached in the files) - not a circle like the other card. The winning design will incorporate the red icon logo on the front and back and include the charity's name, "Light for the Weary Souls" in the same or similar font, as well as an email and phone number. For now, use the email: email@lightfortheweary-mail.org and the phone number 555-382-7194.
We like how the sample business card has transparency, partial and full opacity layers and a matching color scheme. Files will need to be in vector so that our business card printing company can work with it.
UPDATE:
We've some excellent designs in, thank you everyone! I got an early review from the owner, and he requested a minor redirect to find his perfect design. He wants the design to stand out by NOT being a rectangle. Try instead a circle, square, or best yet - something that falls in the outline of the logo icon, either fully or partially. Thank you, everyone!
Light for the Weary Souls text should be incorporated as well as a phone and email.

```html
<!DOCTYPE html>
<html lang="en">
<head>
<meta charset="utf-8">
<title>Light for the Weary Souls – Clear Card</title>
<link href="https://fonts.googleapis.com/css2?family=Poppins:wght@300;400&display=swap" rel="stylesheet">
<style>
  :root {
    --page-bg: #e7e1d8;
    --card-clear: rgba(236, 234, 232, 0.92);
    --card-edge: #9a958f;
    --ink: #1c1c1c;
    --brand-red: #b0161b;
    --brand-red-dark: #6e0a0d;
    --band-text: #f3e6e6;
    --band-text-soft: rgba(243, 230, 230, 0.82);
  }
  html, body {
    margin: 0;
    width: 1200px;
    height: 969px;
    overflow: hidden;
    background: var(--page-bg);
  }
  .stage {
    position: relative;
    width: 1200px;
    height: 969px;
  }
  .card {
    position: absolute;
    left: 190px;
    top: 74px;
    width: 650px;
    height: 650px;
    transform: scale(1.2615);
    transform-origin: 0 0;
    border-radius: 10px;
    background: var(--card-clear);
    box-shadow: inset 0 0 0 1.5px var(--card-edge), 0 8px 24px rgba(60, 45, 30, 0.18);
    overflow: hidden;
    font-family: "Poppins", sans-serif;
  }
  .card-art {
    position: absolute;
    inset: 0;
  }
  .brand-square {
    position: absolute;
    left: 372px;
    top: 118px;
    width: 190px;
    height: 190px;
    background: var(--brand-red);
  }
  .brand-name {
    position: absolute;
    right: 292px;
    top: 232px;
    margin: 0;
    text-align: right;
    font-weight: 400;
    font-size: 41px;
    line-height: 47px;
    color: var(--ink);
    letter-spacing: -0.5px;
    white-space: nowrap;
  }
  .contact {
    position: absolute;
    right: 33px;
    top: 466px;
    margin: 0;
    text-align: right;
    font-weight: 300;
    font-size: 26px;
    line-height: 33px;
    white-space: nowrap;
  }
  .contact .phone { color: var(--band-text); letter-spacing: 1px; }
  .contact .email { color: var(--band-text); }
  .contact .web { color: var(--band-text-soft); }
  .contact span { display: block; }
</style>
</head>
<body>
<main class="stage">
  <section class="card" aria-label="Business card for Light for the Weary Souls">
    <svg class="card-art" viewBox="0 0 650 650" width="650" height="650" aria-hidden="true">
      <defs>
        <radialGradient id="band-glow" cx="0.35" cy="0.3" r="0.8">
          <stop offset="0" stop-color="#c1252b"/>
          <stop offset="0.55" stop-color="#8f1115"/>
          <stop offset="1" stop-color="#620a0c"/>
        </radialGradient>
      </defs>
      <path class="contact-band"
            d="M122 390 L127 417 L650 417 L650 617 L40 617 Q24 617 30 603 Z"
            fill="url(#band-glow)"/>
    </svg>

    <div class="brand-square"></div>
    <h1 class="brand-name">Light for the<br>Weary Souls</h1>

    <p class="contact">
      <span class="phone">555-382-7194</span>
      <span class="email">email@lightfortheweary-mail.org</span>
      <span class="web">www.lightforthewearysouls.org</span>
    </p>
  </section>
</main>
</body>
</html>
```